Zia Dorvelli's Crostalines

Looking for a packaging Label for Italian cookies. It has started with my great grandmothers Pizzelle recipe. Recipe has been in the family for over 100 years.
The packaging will be either clear plastic bags or Clear plastic hinged containers. Hoping for something elegant but traditional Italian. I have attached the company logo for color and idea possibilities
Would also like to give donation to helping animal foundations

Target Market(s)

Cookie lovers, coffee and tea drinkers, lighter alternative to heavy cookies

Requirements
Nice to have
• Family, Italian tradition

```html
<!DOCTYPE html>
<html lang="en">
<head>
<meta charset="utf-8">
<title>Zia Dorvelli's Crostalines – Pizzelle Label</title>
<link rel="stylesheet" href="https://fonts.googleapis.com/css2?family=Playfair+Display:wght@700;900&family=Playball&family=Libre+Caslon+Text&family=Roboto:wght@500&family=Open+Sans&display=swap">
<style>
  :root {
    --backdrop: #c49a6c;
    --label-brown: #7f4b23;
    --label-shadow: #a57d55;
    --rim-tan: #d6b48a;
    --muted-tan: #c4a177;
    --white: #ffffff;
    --orange: #f7941d;
    --brand-orange: #e8571e;
    --band-blue: #27a8e0;
    --flag-green: #009246;
    --flag-red: #ce2b37;
  }
  html, body {
    margin: 0;
    padding: 0;
    width: 1200px;
    height: 1200px;
    overflow: hidden;
    background: var(--backdrop);
  }
  .label {
    display: block;
    width: 1200px;
    height: 1200px;
  }
  .brand-name {
    font-family: "Playfair Display", serif;
    font-weight: 700;
    font-size: 40px;
    fill: var(--brand-orange);
  }
  .brand-tagline {
    font-family: "Open Sans", sans-serif;
    font-size: 17px;
    fill: var(--brand-orange);
  }
  .badge-arc {
    font-family: "Libre Caslon Text", serif;
    font-size: 12px;
    letter-spacing: 2px;
    fill: var(--muted-tan);
  }
  .badge-number {
    font-family: "Libre Caslon Text", serif;
    font-size: 30px;
    fill: var(--muted-tan);
  }
  .claim {
    font-family: "Libre Caslon Text", serif;
    font-size: 18px;
    letter-spacing: 0.5px;
    fill: var(--muted-tan);
  }
  .product-title {
    font-family: "Playfair Display", serif;
    font-weight: 900;
    font-size: 104px;
    letter-spacing: 2px;
    fill: var(--white);
  }
  .product-title-echo {
    font-family: "Playfair Display", serif;
    font-weight: 900;
    font-size: 104px;
    letter-spacing: 2px;
    fill: none;
    stroke: var(--muted-tan);
    stroke-width: 2;
  }
  .product-subtitle {
    font-family: "Playball", cursive;
    font-size: 58px;
    fill: var(--orange);
  }
  .flavour {
    font-family: "Libre Caslon Text", serif;
    font-size: 54px;
    fill: var(--white);
  }
  .net-weight {
    font-family: "Roboto", sans-serif;
    font-weight: 500;
    font-size: 28px;
    fill: var(--white);
  }
</style>
</head>
<body>
<svg class="label" viewBox="0 0 1200 1200" xmlns="http://www.w3.org/2000/svg">
  <defs>
    <clipPath id="label-disc">
      <circle cx="600" cy="615" r="351"/>
    </clipPath>
    <clipPath id="label-inner">
      <circle cx="600" cy="615" r="326"/>
    </clipPath>
    <path id="badge-top-arc" d="M314,499 A54,54 0 0 1 422,499"/>
    <path id="badge-bottom-arc" d="M309,499 A59,59 0 0 0 427,499"/>
  </defs>

  <!-- label disc -->
  <circle class="label-shadow" cx="604" cy="622" r="352" fill="var(--label-shadow)" opacity="0.6"/>
  <circle class="label-body" cx="600" cy="615" r="351" fill="var(--label-brown)"/>
  <circle class="label-rim" cx="600" cy="615" r="333" fill="none" stroke="var(--rim-tan)" stroke-width="2"/>
  <circle class="label-rim-inner" cx="600" cy="615" r="326" fill="none" stroke="var(--rim-tan)" stroke-width="1"/>

  <!-- flavour band -->
  <g clip-path="url(#label-disc)">
    <rect class="flavour-band" x="240" y="763" width="720" height="77" fill="var(--band-blue)"/>
  </g>

  <!-- brand shield -->
  <path class="brand-shield" fill="var(--white)"
        d="M452,268 V522 Q452,552 482,553 Q562,553 590,566 L601,573 L612,566 Q640,553 720,553 Q750,552 750,522 V268 Z"/>

  <!-- brand name -->
  <g class="brand">
    <text class="brand-name" x="601" y="418" text-anchor="middle">Zia</text>
    <text class="brand-name" x="601" y="466" text-anchor="middle">Dorvelli's</text>
    <text class="brand-tagline" x="601" y="524" text-anchor="middle">Italian Tradition</text>
  </g>

  <!-- heritage badge -->
  <g class="heritage-badge">
    <circle cx="368" cy="499" r="70" fill="none" stroke="var(--muted-tan)" stroke-width="1.5"/>
    <circle cx="311" cy="501" r="2" fill="var(--muted-tan)"/>
    <circle cx="425" cy="501" r="2" fill="var(--muted-tan)"/>
    <text class="badge-arc"><textPath href="#badge-top-arc" startOffset="50%" text-anchor="middle">FAMILY RECIPE</textPath></text>
    <text class="badge-arc"><textPath href="#badge-bottom-arc" startOffset="50%" text-anchor="middle">YEAR OLD</textPath></text>
    <text class="badge-number" x="368" y="510" text-anchor="middle">100</text>
  </g>

  <!-- Italian flag -->
  <g class="italian-flag" clip-path="url(#label-inner)">
    <rect x="791" y="328" width="25" height="104" fill="var(--flag-green)"/>
    <rect x="816" y="328" width="25" height="104" fill="var(--white)"/>
    <rect x="841" y="328" width="25" height="104" fill="var(--flag-red)"/>
  </g>

  <!-- claims -->
  <text class="claim" x="833" y="506" text-anchor="middle">HANDMADE</text>
  <text class="claim" x="833" y="535" text-anchor="middle">DELICIOUS</text>

  <!-- product naming -->
  <text class="product-title-echo" x="604" y="682" text-anchor="middle">PIZZELLE</text>
  <text class="product-title" x="599" y="677" text-anchor="middle">PIZZELLE</text>
  <text class="product-subtitle" x="601" y="726" text-anchor="middle">Italian waffle cookies</text>

  <text class="flavour" x="601" y="820" text-anchor="middle">Vanilla</text>
  <text class="net-weight" x="600" y="890" text-anchor="middle">NET WT. 7oz (200g)</text>
</svg>
</body>
</html>
```